BrivoTerna. Lantern of the Steady Harvest. Business card

Professional business card for BrivoTerna (Lantern of the Steady Harvest)
My rationale: Strategy-> Execution-> Results-> Value that lead to the BrivoTerna name: We put the Lantern of the Steady Harvest.
We deliver value to our customers helping them at defining a good strategy (cyan arrow). 90% of well formulated strategies fail due to poor execution so we also consider strategical execution very important (green arrow). Due to the execution we obtain the results (blue arrow). Finally, the results provide feedback to redefine strategy, and the new strategy has to be executed and new results obtained providing new feedback and on and on. It's like a wheel that finally, must create corporate value: value for shareholders, staholders, employees, providers...-

Target Market(s)

CEOs and steering comitees , invewrnent funds

Industry/Entity Type

Business Consultant

Contact Information for Business Card

Teodoro Vinsquel
CEO & Founder
teodoro.vinsquel@brivoterna-example.com
Mobile: +34 655.803.912
www.brivoterna-example.com

Colors

Designer to choose colors to be used in the design.

Requirements
Nice to have
• Nice to hace the words: Strategy, execution, results
• Nice to vave the claim: Lantern of the Steady Harvest
• The three colors should be shown:
• cyan for STRATEGY
• green for EXECUTION
• blue for RESULTS
Should not have
• Complete black background

```html
<!DOCTYPE html>
<html lang="en">
<head>
<meta charset="utf-8">
<title>BrivoTerna – Business Card</title>
<link href="https://fonts.googleapis.com/css2?family=Open+Sans:wght@400;600;700&display=swap" rel="stylesheet">
<style>
  :root {
    --navy: #233f94;
    --green: #9bca3c;
    --cyan: #29abe2;
    --white: #ffffff;
    --ink: #3a3a3a;
    --backdrop: #e9ebef;
  }
  * { box-sizing: border-box; margin: 0; padding: 0; }
  html, body {
    width: 1200px; height: 1000px; overflow: hidden;
    background: var(--backdrop);
    font-family: "Open Sans", Arial, sans-serif;
  }
  .canvas {
    position: relative; width: 1200px; height: 1000px;
  }
  .card {
    position: absolute; left: 200px; width: 800px; height: 457px;
    border-radius: 22px; overflow: hidden;
    box-shadow: 0 10px 28px rgba(20, 30, 60, 0.22);
  }
  .card-back { top: 30px; background: var(--navy); }
  .card-front { top: 513px; background: var(--white); }

  .back-brand {
    position: absolute; inset: 0;
    display: flex; align-items: center; justify-content: center; gap: 22px;
  }
  .back-brand .brand-dot {
    width: 44px; height: 44px; border-radius: 50%; background: var(--green);
  }
  .back-brand .brand-name {
    color: var(--white); font-weight: 700; font-size: 64px; letter-spacing: -1px;
  }

  .front-wave { position: absolute; left: 0; top: 0; width: 800px; height: 457px; }

  .front-brand {
    position: absolute; left: 60px; top: 150px; width: 280px;
    display: flex; align-items: center; gap: 12px;
  }
  .front-brand .brand-dot {
    width: 22px; height: 22px; border-radius: 50%; background: var(--cyan); flex: none;
  }
  .front-brand .brand-name {
    color: var(--navy); font-weight: 700; font-size: 44px; letter-spacing: -1.5px;
  }

  .divider {
    position: absolute; left: 360px; top: 118px; width: 2px; height: 150px;
    background: var(--green);
  }

  .contact { position: absolute; left: 385px; top: 118px; }
  .contact-name { color: var(--green); font-weight: 700; font-size: 27px; line-height: 1.1; }
  .contact-role { color: var(--ink); font-size: 16px; margin-top: 4px; margin-bottom: 12px; }
  .contact-line {
    display: flex; align-items: center; gap: 9px;
    color: var(--ink); font-size: 16px; line-height: 1.65; font-weight: 400;
  }
  .contact-line svg { width: 14px; height: 14px; flex: none; }
</style>
</head>
<body>
<main class="canvas">

  <section class="card card-back" aria-label="Card back">
    <div class="back-brand">
      <span class="brand-dot"></span>
      <span class="brand-name">BrivoTerna</span>
    </div>
  </section>

  <section class="card card-front" aria-label="Card front">
    <svg class="front-wave" viewBox="0 0 800 457" aria-hidden="true">
      <path d="M0 298 C170 405 470 392 800 393 L800 398 C470 398 190 420 0 325 Z" fill="var(--cyan)"/>
      <path d="M0 318 C190 416 470 400 800 402" fill="none" stroke="var(--green)" stroke-width="5"/>
      <path d="M0 330 C200 425 470 406 800 406 L800 457 L0 457 Z" fill="var(--navy)"/>
    </svg>

    <div class="front-brand">
      <span class="brand-dot"></span>
      <span class="brand-name">BrivoTerna</span>
    </div>

    <div class="divider"></div>

    <div class="contact">
      <p class="contact-name">Teodoro Vinsquel</p>
      <p class="contact-role">CEO &amp; Founder</p>
      <p class="contact-line">
        <svg viewBox="0 0 14 14"><rect x="3.5" y="0.8" width="7" height="12.4" rx="1.4" fill="none" stroke="var(--navy)" stroke-width="1.5"/><circle cx="7" cy="11" r="0.9" fill="var(--navy)"/></svg>
        +34 655.803.912
      </p>
      <p class="contact-line">
        <svg viewBox="0 0 14 14"><rect x="0.5" y="2.5" width="13" height="9" fill="var(--navy)"/><path d="M0.5 2.5 L7 8 L13.5 2.5" fill="none" stroke="var(--white)" stroke-width="1.2"/></svg>
        teodoro.vinsquel@brivoterna-example.com
      </p>
      <p class="contact-line">
        <svg viewBox="0 0 14 14"><circle cx="7" cy="7" r="6.2" fill="none" stroke="var(--navy)" stroke-width="1.4"/><ellipse cx="7" cy="7" rx="2.6" ry="6.2" fill="none" stroke="var(--navy)" stroke-width="1.2"/><line x1="0.8" y1="7" x2="13.2" y2="7" stroke="var(--navy)" stroke-width="1.2"/></svg>
        www.brivoterna-example.com
      </p>
    </div>
  </section>

</main>
</body>
</html>
```